New web design for a service provider in the medical field

We are looking for a new design for our website. We are a company that repairs and sells medical endoscopes. Our customers include doctors and hospitals. Our current website can be found at https://lumavex.de/en/lumavex-english.
We need a new web design (without programming) for the following 3 pages:
-Startpage https://lumavex.de/en/lumavex-english/
-Used endoscopes https://lumavex.de/en/used-endoscopes/
-Purchase https://lumavex.de/en/purchase/
The design should be modern and stylish.
The blue color of the logo should be reflected on the page, but not too intrusive.
I have uploaded the images from the header. If more images are needed, let me know and I will upload them.

Target Market(s)
Doctors and hospitals

```html
<!DOCTYPE html>
<html lang="en">
<head>
<meta charset="utf-8">
<title>Lumavex – Used Endoscopes</title>
<link href="https://fonts.googleapis.com/css2?family=Roboto:wght@400;500;700;900&display=swap" rel="stylesheet">
<style>
:root{
  --navy:#13293d;
  --navy-deep:#0f2236;
  --blue:#2592d8;
  --blue-light:#4aa8e4;
  --ice:#e9eef5;
  --text:#5a6470;
  --white:#ffffff;
}
*{box-sizing:border-box;margin:0;padding:0}
html,body{width:1200px;height:5164px;overflow:hidden}
body{font-family:"Roboto",sans-serif;color:var(--text);background:var(--white);position:relative}
.abs{position:absolute}
h2.section-title{font-weight:700;font-size:29px;line-height:38px;text-align:center;color:var(--navy);text-transform:uppercase;letter-spacing:.5px}
h2.section-title span{color:var(--blue);display:block}
.accent{color:var(--blue)}
p{font-size:13px;line-height:26px}

/* top bar */
.topbar{left:0;top:0;width:1200px;height:92px;background:var(--navy)}
.top-contact{top:9px;height:26px;display:flex;align-items:center;gap:12px;color:#fff;font-size:13px}
.ico-circle{width:26px;height:26px;border-radius:50%;background:#fff;display:flex;align-items:center;justify-content:center;flex:none}
.social{top:8px;display:flex;gap:6px}
.social span{width:28px;height:28px;border-radius:50%;border:2px solid #fff;display:flex;align-items:center;justify-content:center}
.social span.filled{background:var(--blue);border-color:var(--blue)}
.social span i{display:block;width:8px;height:8px;border-radius:50%;background:#fff}
.social span.light i{background:var(--navy)}
.navbar{left:72px;top:46px;width:1054px;height:86px;background:#fff;border-radius:43px;box-shadow:0 6px 20px rgba(0,0,0,.08)}
.brand{left:46px;top:30px;font-weight:700;font-size:18px;color:var(--navy);display:flex;align-items:center;gap:8px}
.brand i{width:14px;height:14px;border-radius:50%;background:var(--blue);display:block}
.nav{right:36px;top:34px;display:flex;gap:34px;font-size:13px;font-weight:500;color:var(--navy);text-transform:uppercase}
.nav .active{color:var(--blue)}

/* hero */
.hero{left:0;top:0;width:1200px;height:560px;
  background:
   radial-gradient(ellipse 160px 120px at 600px 250px,rgba(40,44,50,.75),rgba(40,44,50,0) 100%),
   radial-gradient(ellipse 110px 140px at 1040px 380px,rgba(50,54,60,.7),rgba(50,54,60,0) 100%),
   radial-gradient(ellipse 260px 200px at 520px 300px,rgba(120,126,132,.55),rgba(120,126,132,0) 100%),
   linear-gradient(100deg,#8e979f 0%,#b7bec5 40%,#d5d9dd 70%,#c2c8cd 100%)}
.hero-title{left:108px;top:294px;color:#fff;font-weight:900;font-size:35px;line-height:44px;text-transform:uppercase;text-shadow:0 2px 10px rgba(0,0,0,.15)}
.intro{left:0;top:480px;width:1200px;height:622px;background:linear-gradient(180deg,#f1f5fa,#e8eff7 60%,#f3f6fa)}
.intro-text{left:110px;top:694px;width:494px}
.intro-text h3{font-size:20px;line-height:30px;font-weight:700;color:var(--navy);text-transform:uppercase;margin-bottom:22px}
.intro-text p{font-size:12.5px;line-height:26px;margin-bottom:8px}
.intro-photo{left:660px;top:592px;width:430px;height:430px;border-radius:50%;
  background:
   radial-gradient(ellipse 120px 90px at 250px 300px,#2f8fe0,rgba(47,143,224,0) 100%),
   radial-gradient(ellipse 90px 70px at 130px 330px,#3a9ae6,rgba(58,154,230,0) 100%),
   radial-gradient(ellipse 70px 120px at 260px 140px,#2a3038,rgba(42,48,56,0) 100%),
   linear-gradient(160deg,#f4f6f8,#dde3ea 55%,#c5d0dc)}

/* warranty */
.warranty{left:0;top:1102px;width:1200px;height:726px;background:#fff}
.warranty .section-title{top:88px;left:0;width:1200px}
.warranty p.lead{top:184px;left:120px;width:960px;text-align:center;font-size:12.5px}
.feature{top:324px;width:300px;height:290px;border-radius:34px 34px 0 0;color:#fff;text-align:center;padding-top:30px;background:var(--navy)}
.feature.blue{background:var(--blue)}
.feature .badge{width:98px;height:98px;border-radius:50%;border:2px dashed #fff;margin:0 auto 28px;display:flex;align-items:center;justify-content:center}
.feature .badge span{width:82px;height:82px;border-radius:50%;background:#fff;display:flex;align-items:center;justify-content:center}
.feature h4{font-size:18px;line-height:26px;font-weight:500;text-transform:uppercase}
.feature p{font-size:13px;line-height:24px;margin-top:10px;color:#e4edf6}

/* products */
.products{left:0;top:1828px;width:1200px;height:1944px;background:var(--ice)}
.products .section-title{top:70px;left:0;width:1200px}
.photo{border-radius:18px}
.row-text h3{font-size:27px;font-weight:700;color:var(--navy);text-transform:uppercase;margin-bottom:22px}
.row-text p{font-size:13px;line-height:26px;margin-bottom:24px}
.pills{display:flex;gap:12px}
.pill{height:50px;padding:0 30px;border-radius:25px;display:flex;align-items:center;justify-content:center;font-size:13px;font-weight:700;text-transform:uppercase}
.pill.light{background:#fff;color:var(--navy);box-shadow:0 3px 10px rgba(0,0,0,.08)}
.pill.blue{background:var(--blue);color:#fff}
.pill.navy{background:var(--navy);color:#fff}

/* reasons */
.reasons{left:0;top:3772px;width:1200px;height:690px;background:#fff}
.reasons .section-title{top:78px;left:0;width:1200px;font-size:25px;line-height:34px}
.reason{width:478px;height:196px;background:#fff;border-radius:26px;box-shadow:0 8px 24px rgba(20,40,70,.08);padding:36px 28px 0 104px}
.reason svg{position:absolute;left:28px;top:34px}
.reason h4{font-size:16px;font-weight:700;color:var(--navy);text-transform:uppercase;margin-bottom:14px}
.reason p{font-size:12.5px;line-height:25px;text-align:justify}

/* cta */
.cta{left:0;top:4462px;width:1200px;height:380px;background:
  radial-gradient(ellipse 200px 120px at 820px 200px,rgba(20,60,110,.35),rgba(20,60,110,0) 100%),
  linear-gradient(100deg,#1f86cf,#2b97dc 55%,#2a8fd4)}
.cta h2{top:72px;width:1200px;text-align:center;color:#fff;font-size:31px;font-weight:700}
.cta p{top:128px;left:160px;width:880px;text-align:center;color:#fff;font-size:13px}
.cta .btn{top:212px;left:518px;width:164px;height:46px;border-radius:23px;background:var(--navy);color:#fff;font-size:13px;font-weight:700;display:flex;align-items:center;justify-content:center}

/* footer */
.footer{left:0;top:4790px;width:1200px;height:374px;background:var(--navy)}
.footer h5{font-size:15px;font-weight:500;color:#fff;text-transform:uppercase;margin-bottom:18px}
.footer ul{list-style:none}
.footer li{color:#fff;font-size:13px;line-height:31px;display:flex;align-items:center;gap:14px}
.footer li::before{content:"";width:12px;height:12px;border-radius:50%;border:3px solid var(--blue);box-sizing:border-box}
.contact-line{display:flex;gap:22px;align-items:center;color:#fff;font-size:13px;line-height:20px;margin-bottom:18px}
.contact-line .ico-circle{width:38px;height:38px}
.foot-brand{left:112px;top:166px;font-weight:700;font-size:25px;color:#fff;display:flex;align-items:center;gap:10px}
.foot-brand i{width:18px;height:18px;border-radius:50%;background:var(--blue);display:block}
.foot-rule{left:110px;top:324px;width:980px;height:1px;background:rgba(255,255,255,.2)}
.copyright{top:336px;left:0;width:1200px;text-align:center;color:#fff;font-size:12.5px}
</style>
</head>
<body>

<!-- hero and intro -->
<div class="abs intro"></div>
<div class="abs hero" role="img" aria-label="Photo of an endoscope control head in a clinic, greyscale"></div>
<svg class="abs" style="left:0;top:400px" width="1200" height="200" viewBox="0 0 1200 200" aria-hidden="true">
  <path d="M0 80 C220 0 380 190 620 130 C860 70 1000 -30 1200 20 L1200 200 L0 200Z" fill="#f1f5fa"/>
  <path d="M0 78 C220 -2 380 188 620 128 C860 68 1000 -32 1200 18" fill="none" stroke="#2592d8" stroke-width="6"/>
  <path d="M0 108 C240 28 400 208 640 148 C880 88 1020 8 1200 48" fill="none" stroke="#13293d" stroke-width="3"/>
</svg>
<div class="abs hero-title">Quality without<br>compromise</div>

<div class="abs intro-text">
  <h3>Purchase of used endoscopes – <span class="accent">the inexpensive alternative</span></h3>
  <p>Used endoscopes are an excellent, high-quality alternative to new equipment for all doctors &amp; hospitals who want to add to their equipment pool cost-effectively. On our website you will find all types of equipment - gastroscopes, colposcopes, bronchoscopes, cystoscopes and duodenoscopes.</p>
  <p>All used endoscopes that we offer for sale were already in medical use and have been professionally looked after and serviced during this time. In addition, we can offer you endoscopy accessories both for medical examinations and for cleaning and maintaining your endoscopes.</p>
</div>
<svg class="abs" style="left:640px;top:570px" width="470" height="450" aria-hidden="true">
  <path d="M210 4 A226 226 0 0 1 458 240" fill="none" stroke="#2592d8" stroke-width="26"/>
</svg>
<div class="abs intro-photo" role="img" aria-label="Photo of gloved hands holding a flexible endoscope"></div>

<!-- top bar and navigation -->
<div class="abs topbar"></div>
<div class="abs top-contact" style="left:110px"><span class="ico-circle"><svg width="12" height="12" viewBox="0 0 24 24"><path d="M6.6 10.8a15 15 0 0 0 6.6 6.6l2.2-2.2c.3-.3.7-.4 1-.2 1.1.4 2.3.6 3.6.6.6 0 1 .4 1 1V20c0 .6-.4 1-1 1A17 17 0 0 1 3 4c0-.6.4-1 1-1h3.5c.6 0 1 .4 1 1 0 1.3.2 2.5.6 3.6.1.3 0 .7-.2 1z" fill="#2592d8"/></svg></span>+49 4000 555 120-0</div>
<div class="abs top-contact" style="left:312px"><span class="ico-circle"><svg width="12" height="12" viewBox="0 0 24 24"><path d="M2 5h20v14H2z M2 5l10 8 10-8" fill="none" stroke="#2592d8" stroke-width="2.5"/></svg></span>info@lumavex.de</div>
<div class="abs social" style="left:978px"><span class="filled"><i></i></span><span><i></i></span><span><i></i></span></div>

<div class="abs navbar">
  <div class="abs brand"><i></i>Lumavex</div>
  <div class="abs nav"><span>Home</span><span class="active">Used Endoscopes ⌄</span><span>Endoscopy Accessories ⌄</span><span>Purchase</span><span>Contact us</span></div>
</div>

<!-- warranty -->
<section class="abs warranty">
  <h2 class="abs section-title">Quality with warranty<span>for more safety</span></h2>
  <p class="abs lead">After the purchase, our technicians subjected the devices to extensive technical tests and overhauled them. Last but not least, we rely on well-known brands that themselves stand for a high quality standard – Ovalon, Pelvix and Fynora. For these reasons we can offer a twelve month warranty on our used equipment! Only tested quality leaves our company: To ensure the highest quality standards, we carry out an intensive outgoing inspection on every device before dispatch. We enclose documentation of the test result with your endoscope and archive it for future reference.</p>
  <div class="abs feature" style="left:130px">
    <div class="badge"><span>
      <svg width="46" height="50" viewBox="0 0 46 50"><circle cx="23" cy="19" r="15" fill="none" stroke="#13293d" stroke-width="2.5"/><path d="M23 10l3 6 6 .8-4.5 4.2 1.2 6.2L23 24l-5.7 3.2 1.2-6.2L14 16.8l6-.8z" fill="none" stroke="#13293d" stroke-width="2"/><path d="M13 30l-5 14 7-3 4 6 4-12M33 30l5 14-7-3-4 6-4-12" fill="none" stroke="#13293d" stroke-width="2.5" stroke-linejoin="round"/></svg>
    </span></div>
    <h4>12 months<br>warranty</h4>
    <p>Highest quality standards</p>
  </div>
  <div class="abs feature blue" style="left:450px">
    <div class="badge"><span>
      <svg width="48" height="48" viewBox="0 0 48 48"><path d="M9 26v-4a15 15 0 0 1 30 0v4" fill="none" stroke="#2592d8" stroke-width="2.5"/><rect x="5" y="24" width="8" height="12" rx="3" fill="none" stroke="#2592d8" stroke-width="2.5"/><rect x="35" y="24" width="8" height="12" rx="3" fill="none" stroke="#2592d8" stroke-width="2.5"/><path d="M39 36c0 5-5 7-11 7" fill="none" stroke="#2592d8" stroke-width="2.5"/><rect x="22" y="40" width="7" height="5" rx="2" fill="#2592d8"/></svg>
    </span></div>
    <h4>Best customer<br>service</h4>
    <p>We are there for you - from 08:00<br>to 20:00!</p>
  </div>
  <div class="abs feature" style="left:770px">
    <div class="badge"><span>
      <svg width="50" height="42" viewBox="0 0 50 42"><rect x="3" y="8" width="28" height="22" rx="2" fill="none" stroke="#13293d" stroke-width="2.5"/><path d="M31 15h9l6 7v8H31z" fill="none" stroke="#13293d" stroke-width="2.5" stroke-linejoin="round"/><circle cx="12" cy="33" r="4.5" fill="#fff" stroke="#13293d" stroke-width="2.5"/><circle cx="38" cy="33" r="4.5" fill="#fff" stroke="#13293d" stroke-width="2.5"/><path d="M9 17h14M9 22h9" stroke="#13293d" stroke-width="2.5"/></svg>
    </span></div>
    <h4>Worldwide<br>shipping</h4>
    <p>Our service knows no borders!</p>
  </div>
</section>

<!-- products -->
<section class="abs products">
  <h2 class="abs section-title">Used device - fair price -<span>full performance</span></h2>

  <div class="abs" style="left:110px;top:204px;width:404px;height:372px;border:6px solid var(--blue);border-right:none;border-radius:22px 0 0 22px"></div>
  <div class="abs photo" style="left:132px;top:226px;width:404px;height:352px;background:
    linear-gradient(90deg,rgba(20,22,26,0) 8%,rgba(20,22,26,.75) 12%,rgba(20,22,26,0) 16%,rgba(20,22,26,0) 40%,rgba(20,22,26,.75) 44%,rgba(20,22,26,0) 48%,rgba(20,22,26,0) 82%,rgba(20,22,26,.8) 88%,rgba(20,22,26,0) 94%),
    linear-gradient(135deg,#f3f5f7,#dde1e5 60%,#b8bfc6)" role="img" aria-label="Photo of flexible video endoscopes hanging on a wall"></div>
  <div class="abs row-text" style="left:598px;top:296px;width:492px">
    <h3>Flexible video <span class="accent">endoscopes</span></h3>
    <p style="text-align:justify">Discover our flexible endoscopes from the best brands such as Ovalon, Pelvix and Fynora: gastroscopes, colposcopes, bronchoscopes, duodenoscopes, cystoscopes and more.</p>
    <div class="pills"><div class="pill light">Ovalon</div><div class="pill blue">Pelvix</div><div class="pill navy">Fynora</div></div>
  </div>

  <div class="abs" style="left:684px;top:632px;width:404px;height:372px;border:6px solid var(--navy);border-left:none;border-radius:0 22px 22px 0"></div>
  <div class="abs photo" style="left:662px;top:654px;width:404px;height:352px;background:
    radial-gradient(ellipse 140px 110px at 150px 150px,rgba(30,34,40,.8),rgba(30,34,40,0) 100%),
    radial-gradient(ellipse 90px 90px at 340px 230px,rgba(60,80,110,.8),rgba(60,80,110,0) 100%),
    linear-gradient(135deg,#f4845a,#e2675a 30%,#8a8f9c 60%,#d9e1ea)" role="img" aria-label="Photo of a video processor front panel with a connected cable"></div>
  <div class="abs row-text" style="left:110px;top:738px;width:500px">
    <h3>Processors &amp; <span class="accent">light-sources</span></h3>
    <p>Provide better diagnosis to your patients by means of high-resolution imaging, implemented by the best video processors of the latest generation.</p>
    <div class="pills"><div class="pill light">Ovalon</div><div class="pill blue">Pelvix</div><div class="pill navy">Fynora</div></div>
  </div>

  <div class="abs" style="left:110px;top:1060px;width:404px;height:372px;border:6px solid var(--blue);border-right:none;border-radius:22px 0 0 22px"></div>
  <div class="abs photo" style="left:132px;top:1082px;width:404px;height:352px;background:
    radial-gradient(ellipse 80px 60px at 250px 60px,rgba(40,44,50,.8),rgba(40,44,50,0) 100%),
    radial-gradient(ellipse 70px 120px at 260px 250px,rgba(90,98,110,.6),rgba(90,98,110,0) 100%),
    radial-gradient(ellipse 60px 30px at 130px 220px,rgba(60,120,220,.8),rgba(60,120,220,0) 100%),
    linear-gradient(135deg,#eef1f3,#d3d9de 55%,#a9b3bd)" role="img" aria-label="Photo of a technician working at an endoscopy tower"></div>
  <div class="abs row-text" style="left:598px;top:1150px;width:492px">
    <h3>Endoscopy <span class="accent">systems</span></h3>
    <p style="text-align:justify">We help you with configuring a complete endoscopy system for your needs and requirements - from the endoscope to the peripheral devices (processor, light source, screen, suction pump, etc.).</p>
    <div class="pills"><div class="pill blue" style="padding:0 32px">Learn endoscopy-systems!</div></div>
  </div>

  <div class="abs" style="left:684px;top:1488px;width:404px;height:372px;border:6px solid var(--navy);border-left:none;border-radius:0 22px 22px 0"></div>
  <div class="abs photo" style="left:662px;top:1510px;width:404px;height:352px;background:
    radial-gradient(ellipse 160px 80px at 220px 170px,rgba(20,24,30,.7),rgba(20,24,30,0) 100%),
    radial-gradient(ellipse 40px 40px at 60px 180px,rgba(250,245,235,.9),rgba(250,245,235,0) 100%),
    linear-gradient(135deg,#a8dde0,#5fb5c2 50%,#2f7390)" role="img" aria-label="Photo of endoscope accessories and biopsy tools on a teal cloth"></div>
  <div class="abs row-text" style="left:110px;top:1588px;width:500px">
    <h3>Accesories</h3>
    <p>Cover your needs for consumables for single or multiple specific use - from biopsy forceps to cleaning brushes and much more.</p>
    <div class="pills"><div class="pill blue" style="padding:0 28px">Find your accessories here!</div></div>
  </div>
</section>

<!-- reasons -->
<section class="abs reasons">
  <h2 class="abs section-title">We are your first choice when<span>buying used endoscopy equipment</span></h2>
  <div class="abs reason" style="left:110px;top:182px">
    <svg width="48" height="44" viewBox="0 0 48 44"><rect x="3" y="3" width="42" height="30" rx="3" fill="none" stroke="#2592d8" stroke-width="2.5"/><path d="M8 20h8l3-8 5 14 4-10 3 4h9" fill="none" stroke="#13293d" stroke-width="2.5"/><path d="M18 40h12" stroke="#2592d8" stroke-width="2.5"/></svg>
    <h4>As new equipment</h4>
    <p>The devices have already been in medical use before but were professionally maintained and serviced. Consumable parts were completely renewed after purchase by Lumavex GmbH.</p>
  </div>
  <div class="abs reason" style="left:610px;top:182px">
    <svg width="48" height="48" viewBox="0 0 48 48"><circle cx="24" cy="24" r="9" fill="none" stroke="#13293d" stroke-width="2.5"/><circle cx="24" cy="24" r="18" fill="none" stroke="#2592d8" stroke-width="2.5" stroke-dasharray="6 4"/></svg>
    <h4>Brand manufacturers</h4>
    <p>We primarily offer the brands Ovalon, Pelvix and Fynora, which are characterized by long-lasting quality and whose manufacturers have already earned a good reputation as a result.</p>
  </div>
  <div class="abs reason" style="left:110px;top:400px">
    <svg width="48" height="48" viewBox="0 0 48 48"><rect x="6" y="3" width="30" height="40" rx="2" fill="none" stroke="#2592d8" stroke-width="2.5"/><path d="M12 14h16M12 22h12M12 30h8" stroke="#13293d" stroke-width="2.5"/><circle cx="34" cy="32" r="7" fill="none" stroke="#13293d" stroke-width="2.5"/><path d="M39 37l6 6" stroke="#13293d" stroke-width="2.5"/></svg>
    <h4>Tested and overhauled</h4>
    <p>Our trained technicians have checked and overhauled every device in a variety of ways before it is offered for resale.</p>
  </div>
  <div class="abs reason" style="left:610px;top:400px">
    <svg width="48" height="48" viewBox="0 0 48 48"><path d="M6 44V30M16 44V22M26 44V26M36 44V14" stroke="#2592d8" stroke-width="5"/><path d="M4 24l12-10 10 6 16-14" fill="none" stroke="#13293d" stroke-width="2.5"/><path d="M2 45h44" stroke="#13293d" stroke-width="2.5"/></svg>
    <h4>Trade-in of old devices</h4>
    <p>As an additional service, if you wish, we will trade in your old device. After an assessment, we will easily offset the residual value with your new device.</p>
  </div>
</section>

<!-- call to action -->
<section class="abs cta" role="img" aria-label="Blue-tinted background photo of a clinic">
  <h2 class="abs">HOW CAN WE HELP YOU?</h2>
  <p class="abs">Good morning! We are looking forward to your message! You can get informations on possible or ongoing repairs of your endoscope technique. You can also get an advise on rational inspection intervals and in choosing the right accessories.</p>
  <div class="abs btn">SEND MESSAGE</div>
</section>
<svg class="abs" style="left:0;top:4730px" width="1200" height="110" viewBox="0 0 1200 110" aria-hidden="true">
  <path d="M0 40 C300 120 700 130 1200 0 L1200 110 L0 110Z" fill="#13293d"/>
  <path d="M0 28 C300 108 700 118 1200 -10" fill="none" stroke="#ffffff" stroke-width="5"/>
</svg>

<!-- footer -->
<footer class="abs footer">
  <div class="abs foot-brand"><i></i>Lumavex</div>
  <div class="abs" style="left:368px;top:104px">
    <h5>Quick links</h5>
    <ul><li>Home</li><li>Endoscope Services</li><li>Endoscope Accessories</li><li>Purchase</li><li>Contact Us</li></ul>
  </div>
  <div class="abs" style="left:634px;top:104px">
    <h5>Other links</h5>
    <ul><li>FAQ</li><li>Blog</li><li>Privacy Policy</li><li>Terms &amp; Conditions</li></ul>
  </div>
  <div class="abs" style="left:868px;top:104px">
    <h5>Contact info</h5>
    <div class="contact-line"><span class="ico-circle"><svg width="16" height="16" viewBox="0 0 24 24"><path d="M12 2a7 7 0 0 0-7 7c0 5 7 13 7 13s7-8 7-13a7 7 0 0 0-7-7zm0 9.5A2.5 2.5 0 1 1 12 6.5a2.5 2.5 0 0 1 0 5z" fill="#2592d8"/></svg></span><span>Lindenweg 12, 21400<br>Nordhaven, Germany</span></div>
    <div class="contact-line"><span class="ico-circle"><svg width="15" height="15" viewBox="0 0 24 24"><path d="M6.6 10.8a15 15 0 0 0 6.6 6.6l2.2-2.2c.3-.3.7-.4 1-.2 1.1.4 2.3.6 3.6.6.6 0 1 .4 1 1V20c0 .6-.4 1-1 1A17 17 0 0 1 3 4c0-.6.4-1 1-1h3.5c.6 0 1 .4 1 1 0 1.3.2 2.5.6 3.6.1.3 0 .7-.2 1z" fill="#2592d8"/></svg></span><span>+49 4000 555 120-0</span></div>
    <div class="contact-line"><span class="ico-circle"><svg width="15" height="15" viewBox="0 0 24 24"><path d="M2 5h20v14H2z M2 5l10 8 10-8" fill="none" stroke="#2592d8" stroke-width="2.5"/></svg></span><span>info@lumavex.de</span></div>
  </div>
  <div class="abs foot-rule"></div>
  <div class="abs copyright">© 2022 <b>Lumavex</b> &nbsp;|&nbsp; All Rights Reserved</div>
  <div class="abs social" style="left:976px;top:330px"><span class="filled"><i></i></span><span class="light" style="background:#fff"><i></i></span><span class="light" style="background:#fff"><i></i></span></div>
</footer>

</body>
</html>
```